New business card/stationary for a consulting company

I am looking for a clean and very professional looking business card for my consulting company as well as corresponding stationary. I am uploading our logo. I like simple and powerful for the feel. No graphics but I am open on everything else. Below is my contact information but would like the final to be in a version I can add my employees information into and print. Thank you.

Daniel Whitcombe
dan@ferncliffadvisory.com
2870 North 9th Avenue, Summit Floor, Elm Ridge, Illinois 60531
www.ferncliffadvisory.com

Industry/Entity Type

Consulting

Contact Information for Business Card

Daniel Whitcombe
dan@ferncliffadvisory.com
www.ferncliffadvisory.com

Font styles to use
Serif
Sans Serif

Requirements
Must have
• Our logo and the business card details.
Nice to have
• our website www.ferncliffadvisory.com

```html
<!DOCTYPE html>
<html lang="en">
<head>
<meta charset="UTF-8">
<title>Ferncliff Advisory — Business Card</title>
<link rel="stylesheet" href="https://fonts.googleapis.com/css2?family=Lato:wght@400;700&family=Oswald:wght@600&display=swap">
<style>
  :root {
    --navy: #0b1180;
    --white: #ffffff;
    --backdrop: #e4e5e9;
  }
  * { box-sizing: border-box; margin: 0; padding: 0; }
  html, body {
    width: 1200px; height: 900px; overflow: hidden;
    background: var(--backdrop);
  }
  .canvas {
    position: relative; width: 1200px; height: 900px;
    display: flex; flex-direction: column; align-items: center; justify-content: center;
    gap: 56px;
  }
  .card {
    position: relative;
    width: 640px; height: 366px;
    background: var(--navy);
    color: var(--white);
    box-shadow: 0 10px 24px rgba(0,0,0,0.18);
  }
  .brand {
    position: absolute; left: 0; right: 0;
    display: flex; align-items: center; justify-content: center; gap: 16px;
    font-family: "Lato", sans-serif; font-weight: 400;
    text-transform: uppercase; letter-spacing: 0.14em;
  }
  .brand-mark {
    width: 34px; height: 34px; background: var(--white);
  }
  .card-back .brand { top: 160px; font-size: 30px; }
  .card-front .brand { top: 70px; font-size: 26px; }
  .holder-name {
    position: absolute; left: 34px; top: 218px;
    font-family: "Oswald", sans-serif; font-weight: 600;
    font-size: 32px; line-height: 1; text-transform: uppercase; letter-spacing: 0.01em;
  }
  .divider {
    position: absolute; left: 302px; top: 206px;
    width: 1.5px; height: 104px; background: var(--white);
  }
  .contact {
    position: absolute; left: 326px; top: 210px;
    font-family: "Lato", sans-serif; font-size: 15.5px; line-height: 1.45;
    list-style: none;
  }
  .contact li { display: flex; align-items: center; gap: 8px; }
  .contact .icon { width: 14px; height: 14px; flex: none; }
  .contact .address { display: block; padding-top: 4px; }
</style>
</head>
<body>
<main class="canvas">
  <section class="card card-back" aria-label="Card back">
    <div class="brand"><span class="brand-mark"></span><span class="brand-name">Ferncliff Advisory</span></div>
  </section>

  <section class="card card-front" aria-label="Card front">
    <div class="brand"><span class="brand-mark"></span><span class="brand-name">Ferncliff Advisory</span></div>
    <h1 class="holder-name">Daniel Whitcombe</h1>
    <div class="divider"></div>
    <ul class="contact">
      <li>
        <svg class="icon" viewBox="0 0 14 14" aria-hidden="true">
          <rect x="1" y="3" width="12" height="8" fill="#fff"/>
          <path d="M1 3 L7 8 L13 3" fill="none" stroke="#0b1180" stroke-width="1.2"/>
        </svg>
        dan@ferncliffadvisory.com
      </li>
      <li>
        <svg class="icon" viewBox="0 0 14 14" aria-hidden="true">
          <circle cx="7" cy="7" r="6" fill="#fff"/>
          <path d="M1 7 H13 M7 1 V13 M7 1 C4 4 4 10 7 13 M7 1 C10 4 10 10 7 13" fill="none" stroke="#0b1180" stroke-width="0.9"/>
        </svg>
        www.ferncliffadvisory.com
      </li>
      <li class="address">2870 North 9th Avenue, Summit Floor<br>Elm Ridge, Illinois 60531</li>
    </ul>
  </section>
</main>
</body>
</html>
```